Copper Lantern

Need a business card for our restaurant. Restaurant and Bar in the mountains of North Idaho. Rustic looking card

rustic design, wood and metal looking, primarily neutral colors

• Name, address, phone number, website, email address

```html
<!DOCTYPE html>
<html lang="en">
<head>
<meta charset="utf-8">
<title>Copper Lantern – Business Card</title>
<link href="https://fonts.googleapis.com/css2?family=Lexend:wght@400;600&display=swap" rel="stylesheet">
<style>
  :root {
    --backdrop: #d1d5d7;
    --ink: #1a1a1a;
    --paper: #ffffff;
    --sand-light: #dcc6a0;
    --sand-mid: #c4a884;
    --sand-dark: #a88a72;
  }
  * { margin: 0; padding: 0; box-sizing: border-box; }
  html, body {
    width: 900px; height: 1200px; overflow: hidden;
    background: var(--backdrop);
    font-family: "Lexend", sans-serif;
    color: var(--ink);
  }
  .card {
    position: absolute; left: 136px; width: 630px; height: 358px;
    border-radius: 12px; overflow: hidden;
  }
  .card--front { top: 215px; }
  .card--back { top: 629px; background: var(--paper); }

  .texture {
    position: absolute; inset: 0;
    background:
      radial-gradient(ellipse 55% 45% at 45% 45%, var(--sand-light) 0%, transparent 70%),
      radial-gradient(ellipse 40% 50% at 85% 70%, var(--sand-light) 0%, transparent 70%),
      linear-gradient(135deg, var(--sand-mid), var(--sand-dark) 50%, var(--sand-mid));
  }
  .badge {
    position: absolute; border: 5px solid var(--ink); border-radius: 50%;
    display: flex; align-items: center; justify-content: center; text-align: center;
  }
  .badge--front { width: 266px; height: 266px; left: 180px; top: 46px; }
  .badge--back { width: 214px; height: 214px; left: 62px; top: 72px; }
  .badge-name {
    font-weight: 400; text-transform: uppercase; letter-spacing: 3px; line-height: 1.35;
  }
  .badge--front .badge-name { font-size: 24px; }
  .badge--back .badge-name { font-size: 19px; }

  .details { position: absolute; left: 300px; top: 70px; }
  .person-name { font-size: 24px; font-weight: 600; letter-spacing: 0.5px; line-height: 1.1; }
  .person-role { font-size: 13.5px; margin-top: 3px; }
  .address { font-size: 13.5px; line-height: 23px; margin-top: 38px; letter-spacing: 0.3px; }
  .contacts { list-style: none; margin-top: 17px; font-size: 13.5px; letter-spacing: 0.3px; }
  .contacts li { display: flex; align-items: center; gap: 7px; height: 29.5px; }
  .contacts .phone { letter-spacing: 2px; }
  .contacts svg { width: 15px; height: 15px; flex: none; }
</style>
</head>
<body>
  <section class="card card--front">
    <div class="texture" role="img" aria-label="Warm sandy watercolour wash background"></div>
    <div class="badge badge--front">
      <span class="badge-name">Copper<br>Lantern</span>
    </div>
  </section>

  <section class="card card--back">
    <div class="badge badge--back">
      <span class="badge-name">Copper<br>Lantern</span>
    </div>
    <div class="details">
      <h1 class="person-name">MARK ELLISON</h1>
      <p class="person-role">Founder</p>
      <p class="address">82 Cedar St,<br>Silverton, ID 83867</p>
      <ul class="contacts">
        <li class="phone">
          <svg viewBox="0 0 24 24" aria-hidden="true"><path fill="currentColor" d="M6.6 10.8a15.2 15.2 0 0 0 6.6 6.6l2.2-2.2a1 1 0 0 1 1-.25 11.4 11.4 0 0 0 3.6.57 1 1 0 0 1 1 1V20a1 1 0 0 1-1 1A17 17 0 0 1 3 4a1 1 0 0 1 1-1h3.5a1 1 0 0 1 1 1c0 1.25.2 2.45.57 3.57a1 1 0 0 1-.25 1z"/></svg>
          (208) 555-0147
        </li>
        <li>
          <svg viewBox="0 0 24 24" aria-hidden="true"><path fill="currentColor" d="M2 5h20v14H2z"/><path fill="none" stroke="#fff" stroke-width="2" d="M2 6l10 7 10-7"/></svg>
          info@thecopperlanternidaho.com
        </li>
        <li>
          <svg viewBox="0 0 24 24" aria-hidden="true"><g fill="none" stroke="currentColor" stroke-width="2"><circle cx="12" cy="12" r="10"/><ellipse cx="12" cy="12" rx="4" ry="10"/><path d="M2 12h20M4 7h16M4 17h16"/></g></svg>
          thecopperlanternidaho.com
        </li>
      </ul>
    </div>
  </section>
</body>
</html>
```